Business Card Design Project

We need a Business Card for an Mechanical Engineering firm in Singapore. The design should be Modern & Technical looking, yet eye catching.

Our company deals in Cutting Tools & Machine Accessories for the Manufacturing Industries such as Oil & Gas, Aero Space, etc... For more information on our Company, you can either email me or view our website www.torvalen.com.sg.

We are trying to revamp our image to give our consumers a fresh new perspective to our company, so we welcome all ideas.

Industry/Entity Type

Business

Requirements
Must have
• Must incorporate New Company Logo into the card as shown in Uploaded file.

```html
<!DOCTYPE html>
<html lang="en">
<head>
<meta charset="utf-8">
<title>Torvalen Business Card</title>
<link rel="stylesheet" href="https://fonts.googleapis.com/css2?family=Dosis:wght@500&display=swap">
<style>
  :root {
    --page-bg: #e4e7e8;
    --brand-red: #a51c35;
    --stripe-white: #ffffff;
    --label-text: #ffffff;
  }
  html, body {
    margin: 0;
    padding: 0;
    width: 1200px;
    height: 900px;
    overflow: hidden;
    background: var(--page-bg);
  }
  .business-card {
    position: absolute;
    left: 126px;
    top: 182px;
    width: 948px;
    height: 536px;
    background: repeating-linear-gradient(
      to bottom,
      var(--stripe-white) 0px,
      var(--stripe-white) 6px,
      var(--brand-red) 6px,
      var(--brand-red) 13px
    );
  }
  .website-label {
    position: absolute;
    left: 50%;
    top: 50%;
    transform: translate(-50%, -50%);
    width: 464px;
    height: 72px;
    background: var(--brand-red);
    display: flex;
    align-items: center;
    justify-content: center;
  }
  .website-url {
    font-family: "Dosis", sans-serif;
    font-weight: 500;
    font-size: 34px;
    letter-spacing: 1.5px;
    color: var(--label-text);
  }
</style>
</head>
<body>
  <div class="business-card">
    <div class="website-label">
      <span class="website-url">www.torvalen.com.sg</span>
    </div>
  </div>
</body>
</html>
```